Private Investigation Business Card Design

I need a business card for a new private investigation company named Brisk Inquiries. I perform mainly surveillance jobs, vehicle repossessions, document serves etc. The final design should aim for a professional look. The logo has a magnifying glass with stick man arms and legs and is in a running action to show the "Brisk" aspect of the name. If the colour scheme could remain the same as the website www.briskinquiries-demo.com.au with silvers,blacks and a couple electric blue highlights.
Industry/Entity Type
Business
Contact Information for Business Card
Morgan Kellaway
Brisk Inquiries
0487316204
PO Box 58, Carnwell NSW 2291
info@briskinquiries-demo.com.au
www.briskinquiries-demo.com.au
Look and feel

```html
<!DOCTYPE html>
<html lang="en">
<head>
<meta charset="utf-8">
<title>Brisk Inquiries – Business Card</title>
<link rel="stylesheet" href="https://fonts.googleapis.com/css2?family=Open+Sans:wght@400;600;700&display=swap">
<style>
  :root {
    --page-bg: #2b2c2f;
    --card-white: #ffffff;
    --card-shade: #ececec;
    --silver-dark: #8c8c90;
    --silver-light: #c4c4c7;
    --logo-grey: #77777a;
    --name-grey: #8a8a8a;
    --ink: #111111;
    --rule: #9a9a9a;
    --icon: #8d8d8d;
  }
  * { box-sizing: border-box; margin: 0; padding: 0; }
  html, body { width: 1200px; height: 864px; overflow: hidden; }
  body {
    background: var(--page-bg);
    font-family: "Open Sans", Arial, sans-serif;
    position: relative;
  }
  .card {
    position: absolute;
    width: 580px;
    height: 348px;
    border-radius: 3px;
    overflow: hidden;
  }

  /* Back side */
  .card--back {
    left: 150px;
    top: 50px;
    background: linear-gradient(180deg, var(--silver-dark) 0%, var(--silver-light) 100%);
  }
  .card--back .wordmark {
    position: absolute;
    right: 40px;
    bottom: 46px;
    color: #ffffff;
    font-weight: 700;
    font-size: 50px;
    letter-spacing: 1px;
    line-height: 1;
  }

  /* Front side */
  .card--front {
    left: 470px;
    top: 466px;
    background: linear-gradient(180deg, var(--card-white) 0%, var(--card-shade) 100%);
  }
  .card--front .logo {
    position: absolute;
    left: 130px;
    top: 34px;
    display: flex;
    align-items: center;
    gap: 18px;
  }
  .card--front .wordmark {
    color: var(--logo-grey);
    font-weight: 700;
    font-size: 46px;
    letter-spacing: 1px;
    line-height: 1;
  }
  .card--front .logo-dot {
    width: 30px;
    height: 30px;
    border-radius: 50%;
    background: var(--logo-grey);
  }
  .holder {
    position: absolute;
    left: 22px;
    top: 130px;
  }
  .holder-name {
    color: var(--name-grey);
    font-weight: 600;
    font-size: 19px;
    line-height: 1.1;
  }
  .holder-company {
    color: var(--ink);
    font-size: 14px;
    line-height: 1.3;
  }
  .divider {
    position: absolute;
    left: 230px;
    right: 0;
    top: 198px;
    height: 1px;
    background: linear-gradient(90deg, rgba(154,154,154,0) 0%, var(--rule) 30%, var(--rule) 100%);
  }
  .contact {
    position: absolute;
    right: 20px;
    top: 224px;
    list-style: none;
    text-align: right;
    color: var(--ink);
    font-size: 14.5px;
    line-height: 24px;
  }
  .contact li {
    display: flex;
    justify-content: flex-end;
    align-items: center;
    gap: 8px;
  }
  .contact svg { width: 13px; height: 13px; fill: var(--icon); }
  .contact .no-icon { padding-right: 21px; }
</style>
</head>
<body>

  <section class="card card--back" aria-label="Card back">
    <div class="wordmark">Brisk Inquiries</div>
  </section>

  <section class="card card--front" aria-label="Card front">
    <div class="logo">
      <span class="wordmark">Brisk Inquiries</span>
      <span class="logo-dot"></span>
    </div>

    <div class="holder">
      <p class="holder-name">Morgan Kellaway</p>
      <p class="holder-company">Brisk Inquiries</p>
    </div>

    <div class="divider"></div>

    <ul class="contact">
      <li>0487316204
        <svg viewBox="0 0 16 16" aria-hidden="true"><path d="M2 5c0-2 2-3 6-3s6 1 6 3v1h-3V4.5H5V6H2zM4 7h8l2 6H2z"/></svg>
      </li>
      <li>info@briskinquiries-demo.com.au
        <svg viewBox="0 0 16 16" aria-hidden="true"><path d="M1 3h14v10H1zm1.5 1.5v.4L8 9l5.5-4.1v-.4z"/></svg>
      </li>
      <li>www.briskinquiries-demo.com.au
        <svg viewBox="0 0 16 16" aria-hidden="true"><path d="M6.5 9.5l3-3 1 1-3 3zM4 8l2-2 1 1-2 2a1.4 1.4 0 002 2l2-2 1 1-2 2a2.8 2.8 0 01-4-4zm8 0l-2 2-1-1 2-2a1.4 1.4 0 00-2-2L7 7 6 6l2-2a2.8 2.8 0 014 4z"/></svg>
      </li>
      <li class="no-icon">PO Box 58, Carnwell NSW 2291</li>
    </ul>
  </section>

</body>
</html>
```